Medspa business needs a webpage

we need a website for a new Medspa company based in Lynden, WA called Velora Glow Medical Aesthetics. We offer non surgical, cosmetic procedures as well as medical weight loss. We would like a sleek design, with rich colors (dark, emerald green and gold). The website should list our services, pricing and links to book appointments.

```html
<!DOCTYPE html>
<html lang="en">
<head>
<meta charset="utf-8">
<title>Velora Glow Medical Aesthetics</title>
<link href="https://fonts.googleapis.com/css2?family=Playfair+Display:wght@600;700&family=Inter:wght@400;500;600;700&display=swap" rel="stylesheet">
<style>
:root{
  --backdrop:#6b6b6b;
  --gold:#c8a96b;
  --ink:#10200f;
  --deep:#0d1a15;
  --section:#0f1e18;
  --band:#12241d;
  --card:#0f1d17;
  --line:#26392f;
  --text:#e8e4d8;
  --muted:#c9cbc3;
}
*{box-sizing:border-box;margin:0;padding:0}
html,body{width:1200px;height:2282px;overflow:hidden}
body{background:var(--backdrop);font-family:'Inter',sans-serif;color:var(--text);position:relative}
.page{position:absolute;left:81px;top:81px;width:1037px;height:2118px;background:var(--deep);overflow:hidden;box-shadow:0 6px 24px rgba(0,0,0,.35)}
.wrap{position:absolute;left:221px;width:594px}
a{color:inherit;text-decoration:none}

/* header */
.topbar{position:absolute;left:0;top:0;width:100%;height:37px;background:var(--gold);z-index:3}
.brand{position:absolute;left:221px;top:0;width:94px;height:80px;background:var(--ink);border-radius:0 0 4px 4px;display:flex;flex-direction:column;align-items:center;justify-content:center;gap:6px;z-index:4}
.brand-dot{width:10px;height:10px;border-radius:50%;background:var(--gold)}
.brand-name{font-size:8px;font-weight:500;letter-spacing:1.5px;color:var(--gold);text-align:center;line-height:1.3}
.nav{position:absolute;right:222px;top:0;height:37px;display:flex;align-items:center;gap:24px;font-size:10px;font-weight:600;color:var(--ink)}
.nav .book{background:var(--ink);color:var(--gold);padding:6px 11px;border-radius:14px}

/* hero */
.hero{position:absolute;left:0;top:37px;width:100%;height:470px}
.hero-photo{position:absolute;inset:0;background:radial-gradient(ellipse at 22% 35%,#d3d3d6 0%,#c0c0c4 45%,transparent 70%),linear-gradient(90deg,#c4c4c8 0%,#bebec2 48%,#d9c7b7 62%,#e7d9cc 75%,#ecebe8 88%,#f2f2f2 100%)}
.hero-copy{position:absolute;left:221px;top:144px}
.eyebrow{font-size:16px;font-weight:700;color:var(--gold);display:flex;align-items:center;gap:4px}
.eyebrow::after{content:"";width:32px;height:1.5px;background:var(--gold);margin-top:8px}
.hero h1{font-family:'Playfair Display',serif;font-weight:700;font-size:43px;line-height:51px;color:var(--ink);margin-top:8px}
.hero p{font-size:16px;line-height:23px;color:#1a1f1a;margin-top:10px}
.hero-actions{display:flex;gap:6px;margin-top:15px}
.btn{display:inline-flex;align-items:center;justify-content:center;border-radius:14px;font-size:10px;font-weight:600}
.btn-dark{background:var(--ink);color:var(--gold);height:23px;padding:0 12px}
.btn-gold{background:var(--gold);color:var(--ink);height:23px;padding:0 12px}

/* trust */
.trust{position:absolute;left:0;top:507px;width:100%;height:47px;background:var(--band);border-bottom:1px solid var(--line)}
.pills{position:absolute;left:221px;top:9px;width:594px;display:flex;gap:6px}
.pill{flex:1;height:28px;border:1px solid var(--line);border-radius:14px;display:flex;align-items:center;justify-content:center;font-size:8.5px;font-weight:600}

.title{font-family:'Playfair Display',serif;font-weight:700;font-size:19px;position:relative;padding-left:11px}
.title::before{content:"";position:absolute;left:0;top:0;width:4px;height:4px;background:var(--gold)}

/* services */
.services{position:absolute;left:0;top:554px;width:100%;height:275px;background:var(--section)}
.cards3{display:flex;gap:13px;margin-top:12px}
.card{background:var(--card);border:1px solid var(--line);border-radius:6px;padding:13px 10px}
.svc{flex:1;height:164px}
.card h3{font-family:'Playfair Display',serif;font-size:11px;font-weight:700}
.card p{font-size:8.5px;line-height:14px;color:var(--muted);margin-top:9px}
.card ul{list-style:none;margin-top:8px}
.card li{font-size:8.5px;line-height:14px;color:var(--muted);padding-left:9px;position:relative;margin-bottom:2px}
.card li::before{content:"";position:absolute;left:1px;top:6px;width:2.5px;height:2.5px;border-radius:50%;background:var(--muted)}
.more{display:block;font-size:8px;font-weight:600;color:var(--gold);margin-top:4px}

/* pricing + providers */
.pricing{position:absolute;left:0;top:829px;width:100%;height:757px;background:linear-gradient(180deg,var(--band) 0%,#0f1f18 35%,var(--deep) 100%)}
.cards4{display:flex;gap:13px;margin-top:12px;align-items:stretch}
.price{flex:1;height:178px}
.amount{font-family:'Playfair Display',serif;font-size:15px;font-weight:600;margin-top:8px}
.amount small{font-family:'Inter',sans-serif;font-size:7.5px;color:var(--muted);font-weight:400}
.price ul{margin-top:6px}
.chip{display:inline-flex;height:22px;padding:0 10px;border-radius:11px;background:var(--gold);color:var(--ink);font-size:8px;font-weight:600;align-items:center;margin-top:3px}
.note{font-size:7px;color:var(--muted);margin-top:10px}
.people{display:flex;gap:56px;margin:22px 0 0 22px}
.person{width:247px;height:316px;padding:10px}
.portrait{width:227px;height:227px;border-radius:4px}
.p1{background:linear-gradient(160deg,#a8adb0,#7e8386 55%,#3b3d3f)}
.p2{background:linear-gradient(160deg,#b3b1ad,#8f8d8a 55%,#3c3a39)}
.person h3{margin-top:9px}
.person p{margin-top:7px}

/* cta */
.cta{position:absolute;left:0;top:1586px;width:100%;height:133px;background:var(--band);border-top:1px solid var(--line)}
.cta h2{font-family:'Playfair Display',serif;font-size:20px;font-weight:700}
.cta p{font-size:8.5px;margin-top:10px}
.cta-actions{position:absolute;right:222px;top:52px;display:flex;gap:7px}
.btn-line{border:1px solid var(--gold);color:var(--gold);height:27px;padding:0 9px;border-radius:14px}
.cta .btn-gold{height:27px;padding:0 9px}

/* visit */
.visit{position:absolute;left:0;top:1719px;width:100%;height:347px;background:var(--deep)}
.addr{font-size:8.5px;margin-top:20px}
.dir{font-size:8.5px;font-weight:600;color:var(--gold);margin-top:13px;display:block}
.contact-list{list-style:disc;margin:9px 0 0 22px;font-size:8.5px;font-weight:600;color:var(--gold);line-height:13.8px}
.contact-list li::marker{color:var(--text)}
.form{position:absolute;left:553px;top:35px;width:263px;height:277px;padding:13px 10px}
.form label{display:block;font-size:8.5px;margin-top:8px}
.form label:first-child{margin-top:0}
.field{height:22px;border:1px solid var(--line);border-radius:5px;background:#0b1712;margin-top:5px;font-size:6.5px;color:#8d948f;padding:0 7px;display:flex;align-items:center;justify-content:space-between}
.field.area{height:46px;align-items:flex-start;padding-top:8px;font-family:monospace}
.send{height:21px;border-radius:11px;background:var(--gold);color:var(--ink);font-size:7.5px;font-weight:700;display:flex;align-items:center;justify-content:center;margin-top:5px}
.form small{display:block;font-size:7px;color:var(--muted);margin-top:10px}

/* footer */
.footer{position:absolute;left:0;top:2066px;width:100%;height:52px;background:#0b1611;border-top:1px solid var(--line)}
.footer .wrap{top:20px;display:flex;justify-content:space-between;font-size:8.5px}
.footer nav{display:flex;gap:9px}
</style>
</head>
<body>
<div class="page">
  <header class="topbar">
    <div class="brand"><span class="brand-dot"></span><span class="brand-name">VELORA GLOW</span></div>
    <nav class="nav"><a>Home</a><a>Services</a><a>Pricing</a><a>Team</a><a>Contact</a><a class="book">Book Now</a></nav>
  </header>

  <section class="hero">
    <div class="hero-photo" role="img" aria-label="Photo of a provider in a white coat examining a smiling client's jawline in a bright clinic"></div>
    <div class="hero-copy">
      <div class="eyebrow">ELEVATE YOUR SKIN.</div>
      <h1>Enhance Your<br>Confidence.</h1>
      <p>Non-surgical aesthetic treatments and<br>medical weight loss in Lynden, WA.</p>
      <div class="hero-actions"><a class="btn btn-dark">Book an Appointment</a><a class="btn btn-gold">Explore Services</a></div>
    </div>
  </section>

  <div class="trust">
    <div class="pills"><div class="pill">Board-Certified Providers</div><div class="pill">Medical-Grade Treatments</div><div class="pill">Personalized Care Plans</div></div>
  </div>

  <section class="services">
    <div class="wrap" style="top:42px">
      <h2 class="title">Our Services</h2>
      <div class="cards3">
        <article class="card svc"><h3>Injectables</h3><p>Neuromodulators and dermal fillers to smooth lines, restore volume, and refine contours.</p><ul><li>Neurotoxin Treatments</li><li>Lip &amp; Cheek Filler</li><li>Jawline &amp; Chin Contour</li></ul><a class="more">Book injectables →</a></article>
        <article class="card svc"><h3>Skin Rejuvenation</h3><p>Treat texture, tone, and radiance with non-invasive solutions and minimal downtime.</p><ul><li>Microneedling</li><li>Medical-grade Peels</li><li>LED &amp; Collagen Therapy</li></ul><a class="more">Book skin rejuvenation →</a></article>
        <article class="card svc"><h3>Medical Weight Loss</h3><p>Clinically guided programs tailored to your goals with ongoing provider support.</p><ul><li>Consultation &amp; Labs</li><li>GLP-1 Assisted Plans</li><li>Nutrition &amp; Coaching</li></ul><a class="more">Book weight loss consult →</a></article>
      </div>
    </div>
  </section>

  <section class="pricing">
    <div class="wrap" style="top:44px">
      <h2 class="title">Transparent Pricing</h2>
      <div class="cards4">
        <article class="card price"><h3>Neuromodulators</h3><div class="amount">$12–$14 <small>/unit</small></div><ul><li>Forehead, Glabella, Crow's Feet</li><li>Treatment plan review</li><li>Follow-up tweak within 2 weeks</li></ul><a class="chip">Book</a></article>
        <article class="card price"><h3>Dermal Fillers</h3><div class="amount">$650–$800 <small>/syringe</small></div><ul><li>Lips, Cheeks, Jawline, Chin</li><li>Includes numbing &amp; aftercare</li><li>1:1 aesthetic mapping</li></ul><a class="chip">Book</a></article>
        <article class="card price"><h3>Microneedling</h3><div class="amount">$299 <small>/session</small></div><ul><li>Face &amp; Neck</li><li>Medical-grade serums</li><li>Series packages available</li></ul><a class="chip">Book</a></article>
        <article class="card price"><h3>Weight Loss Program</h3><div class="amount">$249 <small>/month</small></div><ul><li>Provider consult &amp; labs</li><li>Medication when appropriate</li><li>Coaching &amp; check-ins</li></ul><a class="chip">Start Now</a></article>
      </div>
      <p class="note">* Pricing shown for contest demo. Final quotes provided after consultation.</p>

      <h2 class="title" style="margin-top:86px">Meet Your Providers</h2>
      <div class="people">
        <article class="card person"><div class="portrait p1" role="img" aria-label="Portrait of Maya Reddin, ARNP, in a dark blazer"></div><h3>Maya Reddin, ARNP</h3><p>Board-certified nurse practitioner specializing in injectables and regenerative skin health.</p></article>
        <article class="card person"><div class="portrait p2" role="img" aria-label="Portrait of Elena Marquez, PA-C, in a dark blazer"></div><h3>Elena Marquez, PA-C</h3><p>Physician associate focused on dermatology, laser-free rejuvenation, and patient education.</p></article>
      </div>
    </div>
  </section>

  <section class="cta">
    <div class="wrap" style="top:40px"><h2>Ready to glow?</h2><p>Reserve your appointment in minutes. New patients welcome.</p></div>
    <div class="cta-actions"><a class="btn btn-gold">Book Online</a><a class="btn btn-line">Call (360) 555-0187</a></div>
  </section>

  <section class="visit">
    <div class="wrap" style="top:42px">
      <h2 class="title">Visit Us</h2>
      <p class="addr">27 Cedar Grove Ave, Lynden, WA 98200</p>
      <a class="dir">Get directions →</a>
      <ul class="contact-list"><li>Call: (360) 555-0187</li><li>Email: hello@veloraglow.com</li><li>Book online</li></ul>
    </div>
    <form class="card form">
      <label>Name</label><div class="field">Your full name</div>
      <label>Email</label><div class="field">you@example.com</div>
      <label>Service</label><div class="field" style="color:var(--text)">Injectables<span>⌄</span></div>
      <label>Message</label><div class="field area">Tell us your goals</div>
      <div class="send">Send Message</div>
      <small>Demo form for contest—replace with platform form or CRM embed.</small>
    </form>
  </section>

  <footer class="footer">
    <div class="wrap"><span>© 2025 Velora Glow Medical Aesthetics • Lynden, WA</span><nav><a>Services</a><a>Pricing</a><a>Book</a><a>Privacy</a></nav></div>
  </footer>
</div>
</body>
</html>
```